business card - Helicopter Flight Services, Flight School, etc.

We need a business card design for a new helicopter service.

We offer Helicopter Flight Services, Aerial Filming & Photography, Flight School, and Helicopter Tours. In that order.

Summit BladeAir, Inc.
Dennis Tollerby
SummitBladeair@Kestmail.com
626-418-7352

Based at the Brenwick Airport in Van Nuys, CA. The final design should communicate integrity and safety. Pictures or logos at your discretion.

Card back side - surprise me.

```html
<!DOCTYPE html>
<html lang="en">
<head>
<meta charset="utf-8">
<title>Summit BladeAir, Inc. – Business Card</title>
<link rel="stylesheet" href="https://fonts.googleapis.com/css2?family=Open+Sans:wght@400;600;700&display=swap">
<style>
  :root {
    --stage: #000000;
    --card: #303135;
    --accent: #1a8ae6;
    --text: #f2f2f2;
    --rule: #2a5f8f;
  }
  * { margin: 0; padding: 0; box-sizing: border-box; }
  html, body {
    width: 1200px; height: 900px; overflow: hidden;
    background: var(--stage);
    font-family: "Open Sans", Arial, sans-serif;
  }
  .stage { position: relative; width: 1200px; height: 900px; }
  .card {
    position: absolute; top: 271px;
    width: 457px; height: 281px;
    background: var(--card);
    border-radius: 14px;
  }
  .card--front { left: 137px; }
  .card--back { left: 626px; }

  .brand {
    position: absolute;
    display: flex; align-items: center; gap: 10px;
    color: var(--accent);
    font-weight: 600;
    font-size: 18px;
    line-height: 1.2;
  }
  .brand__dot {
    width: 14px; height: 14px; border-radius: 50%;
    background: var(--accent); flex: none;
  }
  .card--front .brand { left: 34px; top: 122px; }
  .card--back .brand { left: 22px; top: 122px; }

  .divider {
    position: absolute; left: 220px; top: 97px;
    width: 1px; height: 94px; background: var(--rule);
  }
  .holder {
    position: absolute; left: 234px; top: 100px;
    color: var(--accent); font-weight: 700; font-size: 16.5px;
  }
  .contact {
    position: absolute; left: 234px; top: 153px;
    list-style: none; color: var(--text); font-size: 12.5px;
  }
  .contact li { display: flex; align-items: center; gap: 7px; height: 19.5px; }
  .contact svg { width: 11px; height: 11px; flex: none; }

  .services {
    position: absolute; left: 247px; top: 96px;
    list-style: none; color: var(--text); font-size: 12.5px;
  }
  .services li { display: flex; align-items: center; gap: 6px; height: 25.7px; }
  .services li::before {
    content: ""; width: 8px; height: 8px; border-radius: 50%;
    background: var(--accent); flex: none;
  }
</style>
</head>
<body>
<main class="stage">
  <section class="card card--front">
    <div class="brand"><span class="brand__dot"></span><span>Summit BladeAir,<br>Inc.</span></div>
    <div class="divider"></div>
    <h1 class="holder">Dennis Tollerby</h1>
    <ul class="contact">
      <li>
        <svg viewBox="0 0 24 24" aria-hidden="true"><path fill="#1a8ae6" d="M6.6 10.8a15.1 15.1 0 0 0 6.6 6.6l2.2-2.2a1 1 0 0 1 1-.25 11.4 11.4 0 0 0 3.6.57 1 1 0 0 1 1 1V20a1 1 0 0 1-1 1A17 17 0 0 1 3 4a1 1 0 0 1 1-1h3.5a1 1 0 0 1 1 1c0 1.25.2 2.45.57 3.57a1 1 0 0 1-.25 1z"/></svg>
        <span>626-418-7352</span>
      </li>
      <li>
        <svg viewBox="0 0 24 24" aria-hidden="true"><path fill="#1a8ae6" d="M2 5h20v14H2z"/><path fill="none" stroke="#303135" stroke-width="2" d="M2 5l10 8 10-8"/></svg>
        <span>SummitBladeair@Kestmail.com</span>
      </li>
    </ul>
  </section>

  <section class="card card--back">
    <div class="brand"><span class="brand__dot"></span><span>Summit BladeAir,<br>Inc.</span></div>
    <ul class="services">
      <li>Flight School</li>
      <li>Helicopter Tours</li>
      <li>Helicopter Flight Services</li>
      <li>Aerial Filming &amp; Photography</li>
    </ul>
  </section>
</main>
</body>
</html>
```